design a construction company business card

Design business card around our logo. Card must have all the typical info: name, title, address, phone, email, business name, etc. Somewhere on the card I would like to see our motto "Grounded in trust... Driven by dedication." Consider adding a splash of bright orange to the card to complement the blues and silvers/grays in the logo. We are open to metallic inks, textures, etc. We would like to see options on both light and dark backgrounds. The font in the logo is Euro Technic Extended Regular.

```html
<!DOCTYPE html>
<html lang="en">
<head>
<meta charset="utf-8">
<title>Hollis Builders, Inc. — Business Card</title>
<link rel="stylesheet" href="https://fonts.googleapis.com/css2?family=Michroma&display=swap">
<style>
  :root {
    --backdrop: #3a3a3c;
    --brand-blue: #1c5fbf;
    --brand-blue-deep: #1a3f9c;
    --brand-blue-light: #2a7ad8;
    --card-white: #ffffff;
    --band-gray: #f0f0f2;
    --text-gray: #5f6166;
    --text-dark: #2f3136;
    --motto-white: #eaf1ff;
  }
  * { box-sizing: border-box; margin: 0; padding: 0; }
  html, body {
    width: 1200px; height: 800px; overflow: hidden;
    background: var(--backdrop);
    font-family: "Michroma", sans-serif;
  }
  .canvas {
    width: 1200px; height: 800px;
    display: flex; flex-direction: column; align-items: center; justify-content: center;
    gap: 36px;
  }
  .card {
    position: relative;
    width: 600px; height: 343px;
    overflow: hidden;
    box-shadow: 0 10px 24px rgba(0,0,0,.35);
  }

  /* Front */
  .card-front {
    background: radial-gradient(ellipse at 45% 30%, var(--brand-blue-light) 0%, var(--brand-blue) 45%, var(--brand-blue-deep) 100%);
  }
  .front-map {
    position: absolute; inset: 0;
    background: linear-gradient(160deg, rgba(255,255,255,.05), rgba(0,0,0,.06));
  }
  .front-brand {
    position: absolute; left: 0; right: 0; top: 130px;
    display: flex; align-items: center; justify-content: center; gap: 12px;
  }
  .brand-square { width: 14px; height: 14px; background: var(--card-white); flex: none; }
  .brand-name {
    color: var(--card-white);
    font-size: 24px; letter-spacing: 1px;
    white-space: nowrap;
  }
  .motto {
    position: absolute; left: 0; right: 0; bottom: 42px;
    text-align: center;
    color: var(--motto-white);
    font-size: 11px; letter-spacing: 1.2px;
  }

  /* Back */
  .card-back { background: var(--card-white); }
  .back-band {
    position: absolute; top: 0; bottom: 0; left: 370px; width: 150px;
    background: var(--band-gray);
  }
  .back-band-slim {
    position: absolute; top: 0; bottom: 0; left: 530px; width: 30px;
    background: var(--band-gray);
  }
  .person { position: absolute; left: 40px; top: 70px; }
  .person-name {
    color: var(--brand-blue);
    font-size: 20px; letter-spacing: .5px;
    font-weight: 400;
  }
  .person-title {
    margin-top: 4px;
    color: var(--text-gray);
    font-size: 12px;
  }
  .back-brand {
    position: absolute; right: 34px; top: 150px;
    display: flex; align-items: center; gap: 8px;
  }
  .back-brand .brand-square { width: 10px; height: 10px; background: var(--brand-blue); }
  .back-brand .brand-name { color: var(--brand-blue); font-size: 15px; }

  .contact { position: absolute; left: 40px; bottom: 30px; list-style: none; }
  .contact li {
    display: flex; align-items: flex-start; gap: 12px;
    color: var(--text-dark);
    font-size: 10.5px; line-height: 1.4;
  }
  .contact li + li { margin-top: 3px; }
  .contact .address { margin-bottom: 14px; }
  .contact svg { flex: none; width: 12px; height: 12px; margin-top: 1px; fill: var(--brand-blue); }
  .web-domain { color: var(--brand-blue); }
</style>
</head>
<body>
<main class="canvas">
  <section class="card card-front" aria-label="Card front">
    <div class="front-map" role="img" aria-label="Faint world map texture across the blue background"></div>
    <div class="front-brand">
      <span class="brand-square"></span>
      <span class="brand-name">HOLLIS BUILDERS, INC.</span>
    </div>
    <p class="motto">“Grounded in trust... Driven by dedication.”</p>
  </section>

  <section class="card card-back" aria-label="Card back">
    <div class="back-band"></div>
    <div class="back-band-slim"></div>

    <div class="person">
      <h1 class="person-name">DANIEL REYES</h1>
      <p class="person-title">Ceo &amp; Founder</p>
    </div>

    <div class="back-brand">
      <span class="brand-square"></span>
      <span class="brand-name">HOLLIS BUILDERS, INC.</span>
    </div>

    <ul class="contact">
      <li class="address">
        <svg viewBox="0 0 12 12" aria-hidden="true"><path d="M6 0a4 4 0 0 0-4 4c0 3 4 8 4 8s4-5 4-8a4 4 0 0 0-4-4zm0 5.6A1.6 1.6 0 1 1 6 2.4a1.6 1.6 0 0 1 0 3.2z"/></svg>
        <span>Your Street Address,<br>UnitedStates, 1234</span>
      </li>
      <li>
        <svg viewBox="0 0 12 12" aria-hidden="true"><path d="M2.4 0.6 4.2 2.4 3.2 3.9c.7 1.6 1.9 2.8 3.5 3.5l1.5-1 1.8 1.8-1.3 1.9C5 9.6 1.4 6 .5 1.9z"/></svg>
        <span>000 111 2223</span>
      </li>
      <li>
        <svg viewBox="0 0 12 12" aria-hidden="true"><path d="M0 2h12v8H0zm1 1v.4l5 3.2 5-3.2V3zm0 1.6V9h10V4.6L6 7.8z"/></svg>
        <span>urname@email.com</span>
      </li>
      <li>
        <svg viewBox="0 0 12 12" aria-hidden="true"><circle cx="6" cy="6" r="6"/></svg>
        <span>www.<span class="web-domain">ursitename</span>.com</span>
      </li>
    </ul>
  </section>
</main>
</body>
</html>
```